Refresh Velquor Web Presence - www.velquor-sample.com

Velquor (www.velquor-sample.com)web site needs a makeover. It needs to be more modern, less cluttered, more corporate, prestigious, user friendly, impressive, up to date. We want a modern corporate image that encourages our business users to trust us and buy our products and services. They need to understand that they are dealing with a highly reputable, long established company, but one that is up to date and forward thinking.
1. Clean uncluttered design.
2. Domain Registration box and Countries (price) box to be collapsible and expandable.
3. All links on page need to be conserved for SEO but hidden from view.
4. Logo and general colour scheme need to be retained.
5. Phone number to be prominently displayed at top of page.
6. No calls to action (CTA) below the fold.
7. Sites we like: www.brinzal-sample.com, www.tundexa-sample.com,www.qop.com,www.plavion-sample.com, www.fismet-sample.com (busy but clear CTAs), www.yarmel-sample.com
Reason: We lost a lot of time to review over the holiday weekend. We need to have a chance to interact during business hours.
Target Market(s)
Small business to large enterprise
Industry/Entity Type
Business
Look and feel

```html
<!DOCTYPE html>
<html lang="en">
<head>
<meta charset="utf-8">
<title>Velquor – Domain Names</title>
<link rel="stylesheet" href="https://fonts.googleapis.com/css2?family=Dosis:wght@500;600;700&family=Signika:wght@300;400;600&display=swap">
<style>
:root{
  --navy:#2d3589;
  --bar:#3f4ca6;
  --bar-dark:#323d94;
  --orange:#ec6e12;
  --orange-light:#f6922e;
  --ink:#2a2a2a;
  --line:#cfcfcf;
  --hero-a:#f4f9fd;
  --hero-b:#d3e8f6;
  --art-a:#e9eef2;
  --art-b:#b9c6d2;
  --white:#ffffff;
}
*{box-sizing:border-box;margin:0;padding:0}
html,body{width:1200px;height:1008px;overflow:hidden;background:var(--white);font-family:"Signika",sans-serif;color:var(--ink)}
.page{position:relative;width:1200px;height:1008px}
.abs{position:absolute}

/* utility bar */
.utility-bar{left:0;top:0;width:1200px;height:41px;background:linear-gradient(var(--bar),var(--bar-dark))}
.utility-link{top:11px;color:var(--white);font-size:14px;display:flex;align-items:center;gap:6px}
.whois{left:300px;top:10px;width:160px;height:20px;background:var(--white);font-size:12px;color:#555;padding:3px 7px}
.whois-btn{left:460px;top:10px;width:26px;height:20px;background:var(--orange);display:flex;align-items:center;justify-content:center}
.login{left:1000px;top:0;width:84px;height:41px;background:var(--orange);color:var(--white);font-size:16px;display:flex;align-items:center;justify-content:center;gap:8px}

/* header */
.site-header{left:0;top:41px;width:1200px;height:96px;background:linear-gradient(#ffffff 60%,#ececec)}
.brand{left:96px;top:67px;display:flex;align-items:center;gap:10px;font-weight:600;font-size:40px;color:var(--navy)}
.brand-dot{width:30px;height:30px;border-radius:50%;background:var(--orange)}
.main-nav a{position:absolute;top:86px;font-size:17px;color:var(--ink);text-decoration:none}
.main-nav a.active{color:var(--orange)}
.nav-underline{left:360px;top:114px;width:113px;height:2px;background:var(--orange)}

/* hero */
.hero{left:0;top:137px;width:1200px;height:397px;background:radial-gradient(ellipse at 20% 50%,var(--hero-a),var(--hero-b) 90%)}
.hero-title{left:98px;top:168px;font-family:"Dosis",sans-serif;font-weight:600;color:var(--navy);line-height:1}
.hero-big{font-size:104px;letter-spacing:-1px}
.hero-plus{font-size:62px;font-weight:700;margin-left:2px}
.hero-mid{font-size:70px}
.hero-sub{left:98px;top:372px;font-size:32px;font-weight:300;color:var(--orange)}
.cta{left:101px;top:442px;width:282px;height:58px;border-radius:6px;background:linear-gradient(var(--orange-light),var(--orange));box-shadow:0 2px 4px rgba(0,0,0,.25);color:var(--white);font-family:"Dosis",sans-serif;font-weight:700;font-size:32px;display:flex;align-items:center;padding-left:28px;gap:26px}
.hero-art{left:690px;top:152px;width:380px;height:370px;border-radius:24px;background:linear-gradient(135deg,var(--art-a),var(--art-b))}
.dots{left:560px;top:524px;display:flex;gap:7px}
.dots span{width:15px;height:15px;border-radius:50%;background:#3b3fa8}
.dots span.on{background:var(--orange)}

/* tabs */
.tab{top:586px;height:40px;font-size:20px;color:#3a3a3a;display:flex;align-items:center}
.tab.active{left:94px;width:211px;justify-content:center;background:linear-gradient(#ffffff,#e2e2e2)}
.country{left:916px;top:588px;width:168px;height:32px;border-radius:4px;background:var(--orange);color:var(--white);font-size:17px;display:flex;align-items:center;justify-content:center;gap:8px}

/* search */
.www{left:94px;top:684px;font-family:"Dosis",sans-serif;font-weight:700;font-size:33px;color:var(--navy)}
.search-field{left:200px;top:672px;width:640px;height:64px;border:2px solid var(--line);border-radius:4px;font-size:34px;font-weight:300;color:#9a9a9a;padding:12px 22px}
.search-btn{left:812px;top:672px;width:272px;height:64px}

/* extension table */
.ext-box{left:94px;top:782px;width:990px;height:190px;border:2px solid #d6d6d6;border-radius:4px}
.ext-head{left:96px;top:784px;width:986px;height:42px;background:var(--navy)}
.region{top:794px;color:var(--white);font-size:18px;font-weight:600;display:flex;align-items:center;gap:14px}
.box{width:20px;height:20px;border:1.5px solid #999;background:var(--white);border-radius:2px;position:relative;flex:none}
.region .box{border-color:#ccc}
.ext{font-size:16px;color:#444;display:flex;align-items:center;gap:10px}
.ext.small{font-size:13px;gap:6px}
.tick{position:absolute;left:1px;top:-8px}
</style>
</head>
<body>
<div class="page">

  <div class="abs utility-bar"></div>
  <div class="abs utility-link" style="left:92px">
    <svg width="16" height="14" viewBox="0 0 16 14"><path d="M8 1C4 1 1 3.3 1 6c0 1.5.9 2.8 2.3 3.7L2.6 13l3.6-2.2c.6.1 1.2.2 1.8.2 4 0 7-2.3 7-5S12 1 8 1z" fill="#fff"/></svg>
    Chat with us
  </div>
  <div class="abs utility-link" style="left:210px">
    <svg width="9" height="15" viewBox="0 0 9 15"><rect x="1" y="1" width="7" height="13" rx="1.5" fill="#fff"/><rect x="2.5" y="3" width="4" height="6" fill="#3f4ca6"/></svg>
    Get a Call
  </div>
  <div class="abs whois">Whois Seach</div>
  <div class="abs whois-btn">
    <svg width="13" height="13" viewBox="0 0 13 13"><circle cx="5" cy="5" r="3.5" fill="none" stroke="#fff" stroke-width="2"/><path d="M7.5 7.5 12 12" stroke="#fff" stroke-width="2.4"/></svg>
  </div>
  <div class="abs utility-link" style="left:721px">Register</div>
  <div class="abs utility-link" style="left:790px">Shopping Cart</div>
  <div class="abs utility-link" style="left:900px">View Cart (0)</div>
  <div class="abs login">Login
    <svg width="12" height="8" viewBox="0 0 12 8"><path d="M0 0h12L6 8z" fill="#fff"/></svg>
  </div>

  <div class="abs site-header"></div>
  <div class="abs brand"><span class="brand-dot"></span>Velquor</div>
  <nav class="main-nav">
    <a class="active" style="left:360px">Domain Names</a>
    <a style="left:493px">IDN Domains</a>
    <a style="left:611px">New gTLDs</a>
    <a style="left:713px">Phone Numbers</a>
    <a style="left:852px">Hosting</a>
    <a style="left:930px">Resellers</a>
    <a style="left:1018px">About Us</a>
  </nav>
  <div class="abs nav-underline"></div>
  <svg class="abs" style="left:406px;top:115px" width="16" height="8" viewBox="0 0 16 8"><path d="M0 0h16L8 8z" fill="var(--orange)"/></svg>

  <div class="abs hero"></div>
  <div class="abs hero-title">
    <span class="hero-big">300</span><span class="hero-plus">+</span><span class="hero-mid" style="margin-left:8px">Domain</span><br>
    <span class="hero-mid" style="line-height:.95">Name Extensions</span>
  </div>
  <div class="abs hero-sub">Accredited in over 100 countries</div>
  <div class="abs cta">VIEW PRICING
    <svg width="26" height="28" viewBox="0 0 26 28"><path d="M2 2 24 14 2 26z" fill="#fff"/></svg>
  </div>
  <div class="abs hero-art" role="img" aria-label="Illustration of a world globe surrounded by coloured spheres labelled with domain extensions"></div>
  <div class="abs dots"><span class="on"></span><span></span><span></span></div>

  <div class="abs tab active">Domain Registration</div>
  <div class="abs tab" style="left:318px">IDN</div>
  <div class="abs tab" style="left:377px">Bulk Search</div>
  <div class="abs tab" style="left:511px">Transfer</div>
  <div class="abs tab" style="left:613px">Renew</div>
  <div class="abs tab" style="left:697px">Map Search</div>
  <div class="abs tab" style="left:828px">PhNUM</div>
  <div class="abs country">Select Country
    <svg width="12" height="8" viewBox="0 0 12 8"><path d="M0 0h12L6 8z" fill="#fff"/></svg>
  </div>

  <div class="abs www">www.</div>
  <div class="abs search-field">Search for a new domain</div>
  <svg class="abs search-btn" viewBox="0 0 272 64">
    <defs><linearGradient id="sg" x1="0" y1="0" x2="0" y2="1"><stop offset="0" stop-color="#f6922e"/><stop offset="1" stop-color="#e8650e"/></linearGradient></defs>
    <path d="M0 32 22 0H272V64H22z" fill="url(#sg)"/>
    <text x="56" y="45" font-family="Dosis,sans-serif" font-weight="700" font-size="38" fill="#fff">SEARCH</text>
    <circle cx="223" cy="28" r="10" fill="none" stroke="#fff" stroke-width="4"/>
    <path d="M230 35 241 46" stroke="#fff" stroke-width="5" stroke-linecap="round"/>
  </svg>

  <div class="abs ext-box"></div>
  <div class="abs ext-head"></div>
  <svg class="abs" style="left:150px;top:825px" width="80" height="12" viewBox="0 0 80 12"><path d="M0 0h80L40 12z" fill="var(--navy)"/></svg>

  <div class="abs region" style="left:120px"><span class="box"></span>Generic</div>
  <div class="abs region" style="left:252px"><span class="box"></span>Europe</div>
  <div class="abs region" style="left:379px"><span class="box"><svg class="tick" width="24" height="26" viewBox="0 0 24 26"><path d="M2 15l6 7L22 2" fill="none" stroke="var(--navy)" stroke-width="4"/></svg></span>Asia/Pacific</div>
  <div class="abs region" style="left:545px"><span class="box"></span>America</div>
  <div class="abs region" style="left:682px"><span class="box"></span>Africa</div>
  <div class="abs region" style="left:815px"><span class="box"></span>All Domains</div>

  <div class="abs ext" style="left:130px;top:862px"><span class="box"></span>.biz</div>
  <div class="abs ext" style="left:236px;top:862px"><span class="box"></span>.co</div>
  <div class="abs ext" style="left:348px;top:862px"><span class="box"><svg class="tick" width="24" height="26" viewBox="0 0 24 26"><path d="M2 15l6 7L22 2" fill="none" stroke="var(--navy)" stroke-width="4"/></svg></span>.com</div>
  <div class="abs ext" style="left:462px;top:862px"><span class="box"></span>.info</div>
  <div class="abs ext" style="left:569px;top:862px"><span class="box"></span>.mobi</div>
  <div class="abs ext" style="left:680px;top:862px"><span class="box"><svg class="tick" width="24" height="26" viewBox="0 0 24 26"><path d="M2 15l6 7L22 2" fill="none" stroke="var(--navy)" stroke-width="4"/></svg></span>.name</div>
  <div class="abs ext" style="left:790px;top:862px"><span class="box"></span>.net</div>
  <div class="abs ext" style="left:874px;top:862px"><span class="box"></span>.me</div>
  <div class="abs ext" style="left:960px;top:862px"><span class="box"></span>.org</div>

  <div class="abs ext" style="left:130px;top:914px"><span class="box"></span>.pro</div>
  <div class="abs ext small" style="left:236px;top:914px"><span class="box"></span>.pty-ltd.com</div>
  <div class="abs ext" style="left:352px;top:914px"><span class="box"><svg class="tick" width="24" height="26" viewBox="0 0 24 26"><path d="M2 15l6 7L22 2" fill="none" stroke="var(--navy)" stroke-width="4"/></svg></span>.tel</div>
  <div class="abs ext" style="left:462px;top:914px"><span class="box"></span>.travel</div>
  <div class="abs ext" style="left:569px;top:914px"><span class="box"></span>.xxx</div>

</div>
</body>
</html>
```